Landscape design build company door flyer

I would like this flyer to convey a high-level of professionalism for a company that is excellent with communication with their clients as well as a company that does incredible installations

Went on vacation/holiday

```html
<!DOCTYPE html>
<html lang="en">
<head>
<meta charset="utf-8">
<title>Cedarline Builders – Outdoor Living Flyer</title>
<link href="https://fonts.googleapis.com/css2?family=Catamaran:wght@800&family=Montserrat:wght@400;600;700&display=swap" rel="stylesheet">
<style>
  :root{
    --page-bg:#e6e6e6;
    --paper:#ffffff;
    --navy:#16364c;
    --navy-deep:#0f2c40;
    --navy-glow:#1f5c7a;
    --ink:#1b2f3f;
    --rule-light:#b9c0c6;
    --white:#ffffff;
  }
  *{margin:0;padding:0;box-sizing:border-box}
  html,body{width:1200px;height:1029px;overflow:hidden;background:var(--page-bg)}
  .flyer{position:absolute;left:215px;top:20px;width:770px;height:989px;background:var(--paper);overflow:hidden;
    font-family:"Montserrat",sans-serif;color:var(--ink)}
  .brand{position:absolute;left:0;width:329px;top:128px;text-align:center;
    font-family:"Montserrat",sans-serif;font-weight:700;font-size:17px;letter-spacing:.5px;color:var(--navy)}
  .headline{position:absolute;left:39px;top:184px;font-family:"Catamaran",sans-serif;font-weight:800;
    font-size:38px;line-height:36.5px;color:var(--navy);text-transform:uppercase;letter-spacing:-.3px}
  .divider{position:absolute;left:39px;top:349px;width:257px;height:1px;background:var(--rule-light)}
  .divider::before{content:"";position:absolute;left:0;top:-1px;width:125px;height:3px;background:var(--navy)}
  .intro{position:absolute;left:39px;top:368px;width:258px;font-size:11.4px;line-height:14.7px;text-align:justify;color:var(--ink)}
  .services{position:absolute;left:40px;top:474px;list-style:none}
  .services li{height:34.3px;display:flex;align-items:center;font-weight:700;font-size:15.5px;color:var(--navy);letter-spacing:.2px}
  .services li::before{content:"";display:inline-block;width:2px;height:20px;background:var(--navy);margin-right:8px}
  .contact-panel{position:absolute;left:0;top:720px;width:329px;height:269px;
    background:radial-gradient(ellipse 70% 60% at 45% 55%,var(--navy-glow),var(--navy-deep) 75%);color:var(--white)}
  .areas{position:absolute;left:39px;top:17px;width:260px;font-size:11.8px;line-height:18.4px;font-weight:400}
  .areas strong{font-weight:600}
  .contact-tag{position:absolute;left:39px;top:95px;width:170px;height:21px;background:var(--white);color:var(--navy);
    font-weight:700;font-size:14px;letter-spacing:4.3px;line-height:21px;padding-left:7px}
  .contact-tag::after{content:"";position:absolute;right:-6px;top:0;border-left:6px solid var(--white);border-top:10.5px solid transparent;border-bottom:10.5px solid transparent}
  .contact-line{position:absolute;left:215px;top:105px;width:74px;height:1px;background:#9fb4c2}
  .phone{position:absolute;left:39px;top:145px;display:flex;align-items:center;font-weight:700;font-size:25px;letter-spacing:3px}
  .phone svg{width:22px;height:22px;margin-right:16px}
  .detail{position:absolute;left:43px;display:flex;align-items:center;font-size:12.2px}
  .detail svg{width:13px;height:13px;margin-right:20px}
  .detail.email{top:180px}
  .detail.web{top:202px}
  .photo{position:absolute;left:333px;width:437px;height:245px}
  .photo.p1{top:0;background:linear-gradient(180deg,#4a7cc4 0%,#2c4d7a 35%,#3a4f6e 45%,#5a5652 70%,#6e6862 100%)}
  .photo.p2{top:248px;background:linear-gradient(135deg,#5b6a54 0%,#7aa84a 40%,#8f8f86 65%,#b3b3ad 100%)}
  .photo.p3{top:496px;background:linear-gradient(160deg,#2e3a33 0%,#4a6a7a 35%,#5d5a5a 60%,#7a5a3e 100%)}
  .photo.p4{top:744px;height:245px;background:linear-gradient(170deg,#5a5a50 0%,#a0643c 45%,#c07a46 60%,#5e5a56 100%)}
</style>
</head>
<body>
<main class="flyer">
  <div class="brand">CEDARLINE BUILDERS</div>

  <h1 class="headline">Let’s create<br>your dream<br>outdoor<br>living space!</h1>
  <div class="divider"></div>

  <p class="intro">Discover the endless possibilities for your outdoor space with The Cedarline Builders Team. Our team of skilled artisans is dedicated to turning your outdoor space into a breathtaking oasis that you’ll love coming home to. Our services include:</p>

  <ul class="services">
    <li>PAVER PATIOS</li>
    <li>PAVER DRIVEWAYS</li>
    <li>RETAINING WALLS</li>
    <li>DECKS &amp; RAILINGS</li>
    <li>POOLS</li>
    <li>OUTDOOR LIGHTING</li>
    <li>FIREPITS &amp; FIREPLACES</li>
  </ul>

  <section class="contact-panel">
    <p class="areas">Our service areas include <strong>Bellevue, Issaquah, Kirkland, Redmond, and Sammamish</strong>. We are trusted, tested and reliable with over 20-years experiences.</p>
    <div class="contact-tag">CONTACT US</div>
    <div class="contact-line"></div>
    <div class="phone">
      <svg viewBox="0 0 24 24" aria-hidden="true"><path fill="#fff" d="M6.6 2.2c.6-.3 1.3-.1 1.6.5l2 3.8c.3.6.1 1.2-.4 1.6L8 9.3c1.2 2.6 3.3 4.8 5.8 6.1l1.3-1.8c.4-.5 1.1-.7 1.6-.4l3.8 2c.6.3.8 1 .5 1.6l-1.3 2.7c-.5 1-1.6 1.6-2.7 1.4C9.3 19.6 4.4 14.7 3.1 7c-.2-1.1.4-2.2 1.4-2.7z"/></svg>
      555-014-2876
    </div>
    <div class="detail email">
      <svg viewBox="0 0 16 12" aria-hidden="true"><rect width="16" height="12" rx="1" fill="#fff"/><path d="M1 1l7 5.5L15 1" stroke="#16364c" stroke-width="1.5" fill="none"/></svg>
      hello@cedarlinebuilders.com
    </div>
    <div class="detail web">
      <svg viewBox="0 0 16 16" aria-hidden="true" fill="none" stroke="#fff" stroke-width="1.2"><circle cx="8" cy="8" r="7"/><ellipse cx="8" cy="8" rx="3" ry="7"/><path d="M1 8h14M2.5 4.5h11M2.5 11.5h11"/></svg>
      www.cedarlinebuilders.com
    </div>
  </section>

  <div class="photo p1" role="img" aria-label="Lakeside paver patio with a stone fire pit and cushioned swivel chairs at dusk"></div>
  <div class="photo p2" role="img" aria-label="Backyard with curtained gazebo lounge, stone steps and retaining walls"></div>
  <div class="photo p3" role="img" aria-label="Evening paver terrace with lit seat walls, round fire pit and pool"></div>
  <div class="photo p4" role="img" aria-label="Stepped hardwood deck beside a stone patio and hot tub"></div>
</main>
</body>
</html>
```